Hollendorf Business Card

This is the personal business card for Dr Mark Hollendorf and convers three area of his professional activity - all of them involve (foreign) languages:
o QRVB International Ltd - A translation company with 50 staff. Trades internationally
o WideHarbor Ltd - a global online auction marketplace for translation services (startup)
o Tonal Mosaic - cutting edge technology from the brain sciences which helps learners assimilate the sound patterns of a new language (startup)

Target Market(s)

The card needs to have a "cutting edge" feel - but for a fairly conservative audience - academics, investors.

Industry/Entity Type

Business

Requirements
Must have
• Text:
Dr Mark Hollendorf

Co-founder QRVB International Ltd (Language translation)
Founder WideHarbor Ltd (Translation marketplace)
Founder Tonal Mosaic (Language acquisition)

email: mark.oswin@velmora.co.nz
Phone: +64 21 596 3172
Twitter: @MarkOswin7

```html
<!DOCTYPE html>
<html lang="en">
<head>
<meta charset="utf-8">
<title>Dr Mark Hollendorf – Business Card</title>
<link rel="stylesheet" href="https://fonts.googleapis.com/css2?family=EB+Garamond:wght@400;500&family=Tinos&display=swap">
<style>
  :root {
    --paper: #ffffff;
    --band-top: #a4a684;
    --band-bottom: #d5d7b5;
    --ink: #1a1a1a;
    --olive-text: #7e7c55;
    --mark-tone: #c9c7a2;
  }
  html, body {
    margin: 0;
    padding: 0;
    overflow: hidden;
    background: var(--paper);
  }
  .card {
    position: relative;
    width: 1200px;
    height: 686px;
    background: var(--paper);
    overflow: hidden;
    color: var(--ink);
  }
  .band {
    position: absolute;
    left: 0;
    width: 100%;
  }
  .band--top { top: 0; height: 50px; background: var(--band-top); }
  .band--bottom { bottom: 0; height: 53px; background: var(--band-bottom); }

  .identity {
    position: absolute;
    left: 0;
    width: 680px;
    text-align: center;
    font-family: "EB Garamond", "Times New Roman", serif;
  }
  .brand {
    position: absolute;
    top: 118px;
    left: 200px;
    width: 280px;
    display: flex;
    align-items: center;
    justify-content: center;
    gap: 14px;
    color: var(--mark-tone);
    font-family: "EB Garamond", "Times New Roman", serif;
    font-size: 40px;
    font-weight: 400;
    letter-spacing: 2px;
  }
  .brand__dot {
    width: 18px;
    height: 18px;
    border-radius: 50%;
    background: var(--mark-tone);
  }
  .title-name {
    top: 262px;
    margin: 0;
    font-size: 36px;
    font-weight: 400;
    line-height: 48px;
    letter-spacing: 6px;
    text-transform: uppercase;
    font-variant: small-caps;
  }
  .title-name .line { display: block; }
  .full-name {
    top: 452px;
    margin: 0;
    font-size: 35px;
    font-weight: 500;
    letter-spacing: 5px;
  }
  .profession {
    top: 515px;
    margin: 0;
    font-size: 30px;
    color: var(--olive-text);
    letter-spacing: 0.5px;
  }

  .details {
    position: absolute;
    left: 610px;
    width: 590px;
    text-align: center;
    font-family: "Tinos", "Times New Roman", serif;
  }
  .ventures {
    top: 232px;
    margin: 0;
    padding: 0;
    list-style: none;
    font-size: 22px;
    line-height: 36px;
  }
  .ventures li { margin-bottom: 32px; }
  .ventures li:first-child { margin: 0 auto 32px; width: 470px; }
  .contact {
    top: 452px;
    margin: 0;
    font-size: 28px;
    line-height: 44px;
  }
  .contact p { margin: 0; }
</style>
</head>
<body>
  <div class="card">
    <div class="band band--top"></div>

    <div class="brand">
      <span class="brand__dot"></span>
      <span class="brand__name">Hollendorf</span>
    </div>

    <h1 class="identity title-name">
      <span class="line">Dr. Mark</span>
      <span class="line">Hollendorf</span>
    </h1>
    <p class="identity full-name">Mark Hollendorf</p>
    <p class="identity profession">Profession in Foreign Languages</p>

    <ul class="details ventures">
      <li>Co-founder QRVB International Ltd (Language Translation)</li>
      <li>Founder WideHarbor Ltd (Translation Marketplace)</li>
      <li>Founder Tonal Mosaic (Language Acquisition)</li>
    </ul>

    <div class="details contact">
      <p>Phone: +64 21 596 3172</p>
      <p>Twitter: @MarkOswin7</p>
      <p>E-mail: mark.oswin@velmora.co.nz</p>
    </div>

    <div class="band band--bottom"></div>
  </div>
</body>
</html>
```